Business card design for new eCommerce site focusing on integrity and strong businsess tactics

We need a business card that will stand out and be memorable. Something with color that matches our company logo colors. Think high end version of Pactivo. There are 2 logos provided. The parent company is called Amber Ledge Partners and we are presenting a new and very exciting eCommerce site called BrightHarborTrade.example.

Target Market(s)

Our target markets are in the Activities, Food and Beverage, Health and Beauty

Industry/Entity Type

Marketing

Contact Information for Business Card

We have 4 members that need cards...I will provide all info to the winner of the design contest
Business Address is
4870 West 63rd Avenue, Suite C207
Phoenix AZ 85731

Font styles to use
Serif
Sans Serif

Colors

Designer to choose colors to be used in the design.

Requirements
Must have
• The card must be memorable...should be unique in design but must exude integrity and be playful .
• I have provided several colors or our parent company...please feel free to use which ever
Nice to have
• I will leave this up to you. Feel free to use other images of your choosing that wraps around our client.....Activities, Dining, Health, Beauty
Should not have
• just dont be boring

```html
<!DOCTYPE html>
<html lang="en">
<head>
<meta charset="utf-8">
<title>Business Card – BrightHarborTrade.example</title>
<link href="https://fonts.googleapis.com/css2?family=Arimo:wght@700&family=Oswald:wght@400;500&family=Questrial&display=swap" rel="stylesheet">
<style>
  :root {
    --backdrop: #2e2e2e;
    --card-white: #f7f7f6;
    --brand-blue: #2b7db5;
    --brand-green: #8cc63f;
    --lime: #a9cc48;
    --text-grey: #4a4a4a;
    --rule: #b9b9b9;
    --sky: #41bedb;
  }
  * { margin: 0; padding: 0; box-sizing: border-box; }
  html, body { width: 1200px; height: 960px; overflow: hidden; background: var(--backdrop); }
  .canvas { position: relative; width: 1200px; height: 960px; }

  .card {
    position: absolute;
    width: 600px; height: 342px;
    border-radius: 20px;
    overflow: hidden;
  }
  .card--front { left: 302px; top: 131px; background: var(--card-white); }
  .card--back {
    left: 299px; top: 490px;
    background: linear-gradient(135deg, var(--sky) 0%, var(--brand-blue) 45%, var(--brand-blue) 100%);
  }

  .feature-art {
    position: absolute; left: 10px; top: 8px;
    width: 300px; height: 334px;
    border-radius: 14px 14px 0 0;
    background: linear-gradient(160deg, rgba(140,198,63,0.55) 0%, rgba(140,198,63,0.35) 40%, rgba(43,125,181,0.45) 75%, rgba(43,125,181,0.6) 100%);
  }

  .contact-block {
    position: absolute; right: 32px; top: 34px; width: 240px;
    text-align: right;
    font-family: "Questrial", sans-serif;
    color: var(--text-grey);
  }
  .person-name {
    font-family: "Oswald", sans-serif; font-weight: 500;
    font-size: 25px; line-height: 30px;
    color: var(--brand-blue); letter-spacing: 0.5px;
  }
  .person-role {
    font-size: 15px; line-height: 18px; color: var(--brand-green);
  }
  .divider { border-top: 1px dotted var(--rule); margin: 9px 0 10px; }
  .address-line { font-size: 14.5px; line-height: 18px; }
  .contact-line {
    display: flex; justify-content: flex-end; align-items: center; gap: 8px;
    font-size: 14px; line-height: 19.5px;
  }
  .contact-line svg { width: 13px; height: 13px; fill: var(--brand-blue); flex: none; }

  .site-mark {
    position: absolute; right: 32px; top: 266px;
    display: flex; align-items: center; gap: 8px;
    font-family: "Questrial", sans-serif;
  }
  .site-mark__dot { width: 14px; height: 14px; border-radius: 50%; background: var(--brand-green); flex: none; }
  .site-mark__name { font-size: 18px; color: var(--brand-blue); }
  .site-tagline {
    position: absolute; right: 32px; top: 293px;
    font-family: "Questrial", sans-serif;
    font-size: 10.5px; letter-spacing: 0.6px; color: var(--text-grey);
  }

  .parent-mark__circle {
    position: absolute; left: 228px; top: 70px;
    width: 144px; height: 144px; border-radius: 50%;
    background: var(--lime);
  }
  .parent-mark__name {
    position: absolute; left: 0; right: 0; top: 222px;
    text-align: center;
    font-family: "Arimo", sans-serif; font-weight: 700;
    font-size: 33px; color: var(--lime);
  }
</style>
</head>
<body>
<main class="canvas">

  <section class="card card--front" aria-label="Card front">
    <div class="feature-art" role="img" aria-label="Large decorative figure artwork with green leaves and a blue swoosh"></div>

    <div class="contact-block">
      <p class="person-name">DANA WHITFIELD</p>
      <p class="person-role">CEO/FOUNDER</p>
      <div class="divider"></div>
      <p class="address-line">4870 West 63rd Avenue</p>
      <p class="address-line">Suite C207</p>
      <p class="address-line">Phoenix AZ 85731</p>
      <div class="divider"></div>
      <p class="contact-line">602 555 0148
        <svg viewBox="0 0 24 24" aria-hidden="true"><path d="M6.6 10.8a15 15 0 0 0 6.6 6.6l2.2-2.2a1 1 0 0 1 1-.25 11.4 11.4 0 0 0 3.6.57 1 1 0 0 1 1 1V20a1 1 0 0 1-1 1A17 17 0 0 1 3 4a1 1 0 0 1 1-1h3.5a1 1 0 0 1 1 1c0 1.25.2 2.45.57 3.57a1 1 0 0 1-.25 1z"/></svg>
      </p>
      <p class="contact-line">602 555 0193
        <svg viewBox="0 0 24 24" aria-hidden="true"><path d="M7 1h10a2 2 0 0 1 2 2v18a2 2 0 0 1-2 2H7a2 2 0 0 1-2-2V3a2 2 0 0 1 2-2zm0 3v14h10V4zm5 15.5a1.2 1.2 0 1 0 0 2.4 1.2 1.2 0 0 0 0-2.4z"/></svg>
      </p>
      <p class="contact-line">dana@brightharbortrade.example
        <svg viewBox="0 0 24 24" aria-hidden="true"><path d="M2 5h20v14H2zm2 2v.5l8 5 8-5V7zm0 2.8V17h16V9.8l-8 5z"/></svg>
      </p>
      <p class="contact-line">www.brightharbortrade.example
        <svg viewBox="0 0 24 24" aria-hidden="true"><path d="M12 2a10 10 0 1 0 0 20 10 10 0 0 0 0-20zm-1 17.9A8 8 0 0 1 4.1 11l4.9 4.9v1a2 2 0 0 0 2 2zm6.9-2.5a2 2 0 0 0-1.9-1.4h-1v-3a1 1 0 0 0-1-1H8v-2h2a1 1 0 0 0 1-1V7h2a2 2 0 0 0 2-2v-.4a8 8 0 0 1 2.9 12.8z"/></svg>
      </p>
    </div>

    <div class="site-mark">
      <span class="site-mark__dot"></span>
      <span class="site-mark__name">BrightHarborTrade.example</span>
    </div>
    <p class="site-tagline">Activities-Dining-Health-Beauty</p>
  </section>

  <section class="card card--back" aria-label="Card back">
    <div class="parent-mark__circle"></div>
    <p class="parent-mark__name">Amber Ledge Partners</p>
  </section>

</main>
</body>
</html>
```